1 Page for Computer Repair Website

Looking for a 1 page website with a design that compliments the business card and pamphlet that have already been made (attached files). It should look business professional and easy to read. Email and phone number should be somewhere near the top of the website, visible when the page loads. I don't want any forms for people to mess with. No "Contact Us" form or entering in email for newsletter. Customers will just be looking at this site to confirm we are professionals and have our business in order.

Target Market(s)

Home and small business

Industry/Entity Type

Computer Repair

Coding

Coded - Design and coding required

Number of Pages Required

1 page

Font styles to use
Other font styles liked:
• Helvetica variations used in pamphlet and card

Colors
0455a3
cfdeed
85abd2
3276b5
85cae6
ffffff

Requirements
Must have
• Compliment the pamphlet and business card in color choices and font use. Pleasing to the eye and easy to read through categories and text.
Should not have
• Forms. No "enter name and email here" or anything of the sort.

```html
<!DOCTYPE html>
<html lang="en">
<head>
<meta charset="utf-8">
<title>QUIKBIT Computer Repair</title>
<link href="https://fonts.googleapis.com/css2?family=Roboto:wght@300;400;500;700&display=swap" rel="stylesheet">
<style>
:root{
  --blue-deep:#0455a3;
  --blue-mid:#3276b5;
  --blue-soft:#85abd2;
  --blue-sky:#85cae6;
  --blue-pale:#cfdeed;
  --white:#ffffff;
  --ink:#333840;
  --muted:#7c828a;
  --line:#dfe3e8;
  --gray-band:#f2f3f5;
  --footer:#2c2f33;
  --footer-bottom:#222427;
  --footer-text:#8d9299;
}
*{box-sizing:border-box;margin:0;padding:0}
html,body{width:1200px;height:2564px;overflow:hidden}
body{font-family:"Roboto",Helvetica,Arial,sans-serif;color:var(--ink);background:var(--white)}
a{color:inherit;text-decoration:none}

/* header */
.site-header{height:100px;display:flex;align-items:center;padding:0 84px;border-bottom:1px solid var(--line)}
.brand{font-size:34px;font-weight:500;color:var(--blue-deep);letter-spacing:1px;line-height:1}
.brand small{display:block;font-size:10px;font-weight:400;color:var(--muted);letter-spacing:1px;margin-top:4px}
.main-nav{margin-left:auto;display:flex;align-items:center;gap:14px}
.main-nav a{font-size:12px;font-weight:500;color:var(--ink);padding:8px 12px;text-transform:uppercase}
.main-nav a.active{border:1px solid var(--blue-deep);color:var(--blue-deep)}
.social{display:flex;gap:8px;margin-left:14px}
.social span{width:16px;height:16px;border-radius:50%;background:var(--blue-soft);display:block}
.call-btn{margin-left:16px;background:var(--blue-deep);color:var(--white);font-size:11px;font-weight:500;padding:9px 14px;text-transform:uppercase}

/* hero */
.hero{position:relative;height:560px;background:linear-gradient(90deg,#f1f3f6 0%,#e7ebf0 45%,#dde3ea 100%)}
.hero-photo{position:absolute;right:0;top:0;width:620px;height:100%;background:linear-gradient(120deg,#d9e0e8 0%,#b9c6d4 45%,#8c9fb4 100%)}
.hero-copy{position:absolute;left:84px;top:210px;width:470px}
.hero-copy h1{font-size:38px;font-weight:400;line-height:1.2;color:#2b3138}
.hero-copy h1 strong{color:var(--blue-deep);font-weight:700}
.hero-copy p{font-size:14px;line-height:1.55;color:var(--muted);margin-top:12px}
.btn-primary{display:inline-block;margin-top:28px;background:var(--blue-deep);color:var(--white);font-size:13px;padding:13px 22px}
.scroll-down{position:absolute;left:50%;bottom:-22px;transform:translateX(-50%);width:44px;height:44px;border-radius:50%;background:var(--white);border:1px solid var(--line);display:flex;align-items:center;justify-content:center}

/* section titles */
.section-title{text-align:center}
.section-title h2{font-size:30px;font-weight:400;color:var(--blue-mid);text-transform:uppercase;letter-spacing:1px}
.section-title .tag{display:flex;align-items:center;justify-content:center;gap:14px;margin-top:8px;font-size:13px;letter-spacing:3px;color:var(--muted);text-transform:uppercase}
.section-title .tag::before,.section-title .tag::after{content:"";width:70px;height:1px;background:var(--muted)}

/* about */
.about{height:430px;padding-top:100px;text-align:center}
.about p{width:820px;margin:40px auto 0;font-size:13px;line-height:1.9;color:var(--muted)}
.btn-dark{display:inline-block;margin-top:36px;background:#2a2d31;color:var(--white);font-size:12px;padding:11px 20px;text-transform:uppercase}

/* services */
.services{height:600px;background:var(--gray-band);padding-top:60px;border-top:1px solid var(--line)}
.service-grid{display:flex;justify-content:center;gap:30px;margin-top:60px}
.service{width:220px;text-align:center}
.service-icon{width:70px;height:70px;margin:0 auto;display:flex;align-items:center;justify-content:center;position:relative}
.service-icon::before{content:"";position:absolute;inset:8px;transform:rotate(45deg);background:var(--white);border:1px solid var(--line)}
.service.featured .service-icon::before{background:var(--blue-deep);border-color:var(--blue-deep);box-shadow:0 0 0 5px var(--blue-pale)}
.service-icon svg{position:relative}
.service h3{font-size:15px;font-weight:500;margin-top:24px}
.service.featured h3{color:var(--blue-deep)}
.service p{font-size:12px;line-height:1.7;color:var(--muted);margin-top:12px}
.service .more{display:inline-block;margin-top:26px;font-size:11px;font-weight:500;text-transform:uppercase;color:var(--ink)}
.dots{display:flex;justify-content:center;gap:8px;margin-top:64px}
.dots span{width:9px;height:9px;border-radius:50%;background:var(--blue-soft)}
.dots span.on{background:var(--blue-deep)}

/* why choose us */
.why{height:540px;padding-top:70px;position:relative}
.why-laptop{position:absolute;left:100px;top:200px;width:470px;height:300px;border-radius:10px;background:linear-gradient(135deg,#5a6470 0%,#9aa9b8 40%,#d8dee6 100%)}
.why-panel{position:absolute;left:640px;top:210px;width:460px}
.why-panel .panel-head{background:var(--blue-deep);color:var(--white);font-size:12px;font-weight:500;text-transform:uppercase;padding:16px 20px;display:flex;align-items:center;gap:10px}
.why-panel .panel-body{background:var(--blue-sky);color:var(--white);font-size:12px;line-height:1.7;padding:18px 20px}
.why-panel .item{border:1px solid var(--line);margin-top:12px;padding:14px 20px;font-size:12px;font-weight:500;text-transform:uppercase;display:flex;align-items:center;gap:12px}
.plus{width:16px;height:16px;border:1px solid currentColor;display:flex;align-items:center;justify-content:center;font-size:12px;line-height:1}

/* footer */
.site-footer{height:390px;background:var(--footer);padding:34px 84px 0;display:flex;gap:70px}
.footer-col{width:200px;color:var(--footer-text);font-size:12px;line-height:1.8}
.footer-col h4{color:var(--white);font-size:13px;font-weight:500;text-transform:uppercase;margin-bottom:16px;padding-bottom:10px;border-bottom:1px solid #44484d}
.footer-col ul{list-style:none}
.footer-col li{margin-bottom:8px}
.footer-col p+p{margin-top:14px}
.footer-social{display:flex;gap:6px;margin-top:20px}
.footer-social span{width:20px;height:20px;border-radius:50%;background:#4a4e54;display:block}
.contact-line{display:flex;gap:8px;align-items:center;margin-top:8px}
.contact-line b{color:var(--white);font-weight:500}
.bottom-bar{height:44px;background:var(--footer-bottom);color:var(--footer-text);font-size:11px;display:flex;align-items:center;padding:0 84px}
.bottom-bar nav{margin-left:auto;display:flex;gap:24px}
</style>
</head>
<body>

<header class="site-header">
  <div class="brand">QUIKBIT<small>Computer Repair Service</small></div>
  <nav class="main-nav">
    <a class="active" href="#home">Home</a>
    <a href="#about">About</a>
    <a href="#services">Services</a>
    <a href="#why">Why Choose Us</a>
    <a href="#contact">Contact Us</a>
  </nav>
  <div class="social"><span></span><span></span><span></span></div>
  <a class="call-btn" href="#contact">555-0142-700</a>
</header>

<section class="hero" id="home">
  <div class="hero-photo" role="img" aria-label="Technician repairing the inside of a desktop computer"></div>
  <div class="hero-copy">
    <h1>Protect Your Computer System Across <strong>QUIKBIT</strong> Service.</h1>
    <p>We keep your home and office machines fast, safe and working, with honest repair work done right the first time.</p>
    <a class="btn-primary" href="#services">Fix it out for service</a>
  </div>
  <div class="scroll-down">
    <svg width="14" height="9" viewBox="0 0 14 9"><path d="M1 1l6 6 6-6" fill="none" stroke="#0455a3" stroke-width="2"/></svg>
  </div>
</section>

<section class="about" id="about">
  <div class="section-title">
    <h2>About Us</h2>
    <div class="tag">Lum elit sit amet est aenean eui</div>
  </div>
  <p>We are a local computer repair team serving homes and small businesses. Our technicians handle everything from slow laptops and failed drives to virus cleanup and full office upgrades. We explain each fix in plain words, give fair prices before work starts and return your machine quickly. Every repair is tested before pickup, and we stand behind our work with clear support whenever you need help again.</p>
  <a class="btn-dark" href="#services">Read More</a>
</section>

<section class="services" id="services">
  <div class="section-title">
    <h2>Our Service</h2>
    <div class="tag">Lum elit sit amet est aenean eui</div>
  </div>
  <div class="service-grid">
    <div class="service">
      <div class="service-icon"><svg width="24" height="24" viewBox="0 0 24 24"><path d="M12 2l8 3v6c0 5-4 9-8 11-4-2-8-6-8-11V5z" fill="none" stroke="#333840" stroke-width="1.6"/></svg></div>
      <h3>Malware Removal</h3>
      <p>We clean viruses and spyware, then set up protection so your files stay safe.</p>
      <a class="more" href="#contact">Learn More</a>
    </div>
    <div class="service">
      <div class="service-icon"><svg width="26" height="22" viewBox="0 0 26 22"><rect x="3" y="2" width="20" height="13" fill="none" stroke="#333840" stroke-width="1.6"/><path d="M1 19h24" stroke="#333840" stroke-width="1.6"/></svg></div>
      <h3>PC / Laptop Repair</h3>
      <p>Screens, keyboards, drives and power faults fixed fast with quality parts.</p>
      <a class="more" href="#contact">Learn More</a>
    </div>
    <div class="service featured">
      <div class="service-icon"><svg width="24" height="24" viewBox="0 0 24 24"><path d="M12 20V5M6 11l6-6 6 6" fill="none" stroke="#ffffff" stroke-width="2"/></svg></div>
      <h3>Hardware / Software Upgrade</h3>
      <p>More memory, faster storage and fresh software to give your system new life.</p>
      <a class="more" href="#contact">Learn More</a>
    </div>
    <div class="service">
      <div class="service-icon"><svg width="24" height="24" viewBox="0 0 24 24"><ellipse cx="12" cy="5" rx="8" ry="3" fill="none" stroke="#333840" stroke-width="1.6"/><path d="M4 5v14c0 1.7 3.6 3 8 3s8-1.3 8-3V5M4 12c0 1.7 3.6 3 8 3s8-1.3 8-3" fill="none" stroke="#333840" stroke-width="1.6"/></svg></div>
      <h3>Data Migration</h3>
      <p>We move your files and settings safely from an old computer to a new one.</p>
      <a class="more" href="#contact">Learn More</a>
    </div>
  </div>
  <div class="dots"><span></span><span class="on"></span><span></span><span></span></div>
</section>

<section class="why" id="why">
  <div class="section-title">
    <h2>Why Choose Us</h2>
    <div class="tag">Lum elit sit amet est aenean eui</div>
  </div>
  <div class="why-laptop" role="img" aria-label="Laptop showing a technician at work on a computer"></div>
  <div class="why-panel">
    <div class="panel-head"><span class="plus">&minus;</span>Best services we provide to our customers</div>
    <div class="panel-body">Certified technicians, clear pricing and quick turnaround. We treat every machine with care and keep you informed at each step.</div>
    <div class="item"><span class="plus">+</span>We give our best system support</div>
    <div class="item"><span class="plus">+</span>Lifetime support for clients</div>
  </div>
</section>

<footer class="site-footer" id="contact">
  <div class="footer-col">
    <h4>About QUIKBIT</h4>
    <p>Local computer repair for homes and small offices, with friendly service and fair prices.</p>
    <p>Open six days a week with same day service on most repairs.</p>
    <div class="footer-social"><span></span><span></span><span></span><span></span><span></span><span></span></div>
  </div>
  <div class="footer-col">
    <h4>Quick Links</h4>
    <ul><li>Home</li><li>About Us</li><li>Services</li><li>Why Choose Us</li><li>Contact Us</li></ul>
  </div>
  <div class="footer-col">
    <h4>Our Services</h4>
    <ul><li>Malware Removal</li><li>PC / Laptop Repair</li><li>Hardware Upgrade</li><li>Data Migration</li></ul>
  </div>
  <div class="footer-col">
    <h4>Contact Us</h4>
    <p>240 Harbor Lane, Suite 12, Millbrook, ST 00000</p>
    <div class="contact-line"><b>Ph:</b> 555-0142-700</div>
    <div class="contact-line"><b>Fax:</b> 555-0142-701</div>
    <div class="contact-line"><b>Email:</b> help@quikbit.example</div>
  </div>
</footer>
<div class="bottom-bar">
  <span>Copyright &copy; QUIKBIT Computer Repair. All Rights Reserved.</span>
  <nav><a href="#home">Terms and Condition</a><a href="#home">Legal Document</a><a href="#home">Privacy Policy</a></nav>
</div>

</body>
</html>
```